Website for new dental office

I am Dr. Colin Ashford and am building a new dental practice. I specialize in general dentistry. I am young and have a higher end dental practice incorporating very new technologies and would like my website to reflect that. As many dental patients are older, the website must be very easy to navigate. I would like patients to be able to request appointments, and will eventually add on patient information forms (the health history, etc, that you normally fill out in the practice) from my practice management software, so leave an area for that.

Industry/Entity Type

Building

```html
<!DOCTYPE html>
<html lang="en">
<head>
<meta charset="utf-8">
<title>AshfordDental — General Dentistry</title>
<link rel="stylesheet" href="https://fonts.googleapis.com/css2?family=Open+Sans:wght@300;400;600;700&display=swap">
<style>
:root{
  --blue:#3f75c4;
  --blue-dark:#2f5fa8;
  --blue-text:#2d62b3;
  --gold:#d9a21a;
  --gold-light:#e8b53a;
  --gold-dark:#c98f0c;
  --ink:#333;
  --muted:#777;
  --line:#dcdcdc;
  --page:#f1f1f1;
  --white:#fff;
}
*{box-sizing:border-box;margin:0;padding:0}
html,body{width:788px;height:1200px;overflow:hidden}
body{position:relative;background:var(--page);font-family:Arial,Helvetica,sans-serif;color:var(--ink)}
.abs{position:absolute}
.os{font-family:"Open Sans",Arial,sans-serif}

/* header */
.brand{left:155px;top:22px;display:flex;align-items:center;gap:8px}
.brand-dot{width:40px;height:40px;border-radius:50%;background:#dfe6f0}
.brand-name{font-family:"Open Sans",Arial,sans-serif;font-weight:600;font-size:15px;color:var(--blue-text)}
.social{right:152px;top:5px;display:flex;gap:9px;font-size:6.5px;color:#6d8bbd}
.social span::before{content:"";display:inline-block;width:5px;height:5px;background:#6d8bbd;margin-right:2px;vertical-align:-0.5px}
.chat{left:462px;top:24px;width:92px;height:42px}
.chat-person{left:0;top:2px;width:26px;height:38px;border-radius:13px 13px 4px 4px;background:linear-gradient(#c9a88c,#e5e8ec)}
.chat-q{left:26px;top:4px;font-size:8px;color:var(--blue-text);font-family:"Open Sans",Arial,sans-serif}
.chat-btn{left:28px;top:15px;width:62px;height:24px;border-radius:4px;background:linear-gradient(var(--gold-light),var(--gold-dark));color:#fff;text-align:center;font-family:"Open Sans",Arial,sans-serif;line-height:1}
.chat-btn small{display:block;font-size:5px;padding-top:4px}
.chat-btn b{font-size:8.5px;font-weight:600}
.enq{left:558px;top:32px;border-left:1px solid var(--line);padding-left:6px;font-family:"Open Sans",Arial,sans-serif}
.enq .t{font-size:6.5px;color:var(--blue-text);font-weight:700}
.enq .n{font-size:8px;color:#222;font-weight:600;line-height:11px}

/* nav */
.nav{left:152px;top:72px;width:484px;height:21px;background:linear-gradient(#5b8fd6,var(--blue));border-radius:3px 3px 0 0;display:flex}
.nav a{color:#fff;text-decoration:none;font-family:"Open Sans",Arial,sans-serif;font-size:5.6px;line-height:21px;padding:0 11px;border-right:1px solid rgba(255,255,255,.25)}
.nav a.on{background:linear-gradient(var(--gold-light),var(--gold-dark));color:#5a3e00;font-weight:700;padding:0 12px}

/* hero */
.hero{left:0;top:93px;width:788px;height:219px;background:linear-gradient(90deg,#e3e7ea,#f3f5f6 45%,#e9edf0 80%,#dfe5ea)}
.hero-photo{left:340px;top:93px;width:300px;height:181px;background:radial-gradient(circle at 50% 55%,#e7c9a8,#d8b888 35%,#dfe4ea 75%)}
.hero-copy{left:153px;top:176px;font-family:"Open Sans",Arial,sans-serif}
.hero-copy .a{font-size:14px;color:var(--blue-text);line-height:16px}
.hero-copy .b{font-size:16px;color:var(--gold);font-weight:700;line-height:18px}
.hero-copy .c{font-size:10.5px;color:#666;letter-spacing:-.2px}

/* appointment panel */
.panel{left:152px;top:274px;width:484px;height:142px;background:var(--blue);color:#fff}
.tab-a{left:0;top:0;width:245px;height:31px;padding:9px 13px;font-family:"Open Sans",Arial,sans-serif;font-size:10.5px}
.tab-b{left:245px;top:0;width:239px;height:31px;background:#f2f2f2;padding:8px 12px;font-family:"Open Sans",Arial,sans-serif;font-size:10.5px;color:var(--blue-text);display:flex;align-items:center;gap:8px}
.col-h{font-family:"Open Sans",Arial,sans-serif;font-size:8.5px;display:flex;align-items:center;gap:5px}
.hours{left:13px;top:64px;width:127px;font-size:6.5px}
.hours div{display:flex;justify-content:space-between;height:20px;line-height:18px;border-bottom:1px solid rgba(255,255,255,.7)}
.hours div:last-child{border:none}
.doc-text{left:155px;top:66px;width:102px;font-size:6.5px;line-height:8px}
.btn-w{background:#fff;color:var(--blue-text);font-size:6.5px;text-align:center;line-height:13px;border-radius:1px}
.field{width:87px;height:15px;border:1px solid rgba(255,255,255,.85);font-size:6.5px;line-height:13px;padding-left:4px}

/* section headings */
.sec-h{left:152px;width:484px;text-align:center}
.sec-h h2{font-family:"Open Sans",Arial,sans-serif;font-weight:400;font-size:12.5px;color:var(--blue-text);position:relative}
.sec-h h2::before,.sec-h h2::after{content:"";position:absolute;top:9px;height:1px;width:160px;background:var(--line)}
.sec-h h2::before{left:0}.sec-h h2::after{right:0}
.sec-h p{font-size:6.5px;color:#444;margin-top:1px}

/* service cards */
.card{top:477px;width:117px;height:180px;background:#fff;box-shadow:0 0 3px rgba(0,0,0,.15)}
.card-img{left:0;top:0;width:117px;height:81px}
.card-title{right:6px;top:56px;text-align:right;font-family:"Open Sans",Arial,sans-serif;font-size:10px;font-weight:600;color:var(--blue-text);line-height:12px}
.card-body{left:14px;top:99px;width:96px;font-size:5.3px;line-height:7.6px;color:#333}
.card-foot{left:5px;top:166px;width:112px;height:1px;background:var(--gold)}
.card-more{right:0;top:167px;font-size:5.5px;color:var(--gold-dark);display:flex;align-items:center;gap:4px}
.card-more i{display:block;width:12px;height:11px;background:var(--gold-light)}

/* doctor */
.box{background:#fff;box-shadow:0 0 3px rgba(0,0,0,.12)}
.doc-photo{left:10px;top:17px;width:112px;height:77px;background:linear-gradient(135deg,#d9a63a,#e9dccb 55%,#c8d6e4)}
.doc-name{left:140px;top:30px;font-family:"Open Sans",Arial,sans-serif;line-height:17px}
.doc-name b{font-size:12.5px;color:var(--blue-text);font-weight:600}
.doc-name .l1{font-size:13px;color:#333}
.doc-name .l2{font-size:12px;color:#555;font-weight:300}
.doc-text2{left:12px;top:119px;width:282px;font-size:5.8px;line-height:9.5px;color:#333}
.gold-link{font-family:"Open Sans",Arial,sans-serif;font-size:8.5px;color:var(--gold);border-left:1px solid var(--gold);padding-left:4px}

.appt h3{font-family:"Open Sans",Arial,sans-serif;font-size:12.5px;font-weight:600;color:var(--blue-text)}
.pill{left:17px;width:132px;height:22px;color:#fff;font-family:"Open Sans",Arial,sans-serif;font-size:8px;display:flex;align-items:center;gap:10px;padding-left:7px}
.btn-gold{background:linear-gradient(var(--gold-light),var(--gold));color:#5a3e00;font-family:"Open Sans",Arial,sans-serif;font-size:8.5px;text-align:center;line-height:18px}

/* bottom */
.col-title{font-family:"Open Sans",Arial,sans-serif;font-weight:300;font-size:11.5px;color:var(--blue-text)}
.tweet{left:326px;width:135px;font-size:6.5px;line-height:8.5px}
.tweet small{display:block;margin-top:5px;color:#666;font-size:6px}
.input{background:#fff;border:1px solid #e0e0e0;border-radius:2px;font-size:6.5px;color:#aaa;padding:5px 7px}
.label{font-size:6.5px;color:#333}
.label em{color:#d04040;font-style:normal}

.footer-line{left:0;top:1158px;width:788px;height:1px;background:#ddd}
.footer-copy{left:153px;top:1168px;font-size:6px;color:#777}
.to-top{left:680px;top:1163px;width:18px;height:18px;border-radius:50%;background:var(--blue)}
.footer-bar{left:0;top:1186px;width:788px;height:14px;background:var(--blue)}
</style>
</head>
<body>

<!-- header -->
<div class="abs brand"><span class="brand-dot"></span><span class="brand-name">AshfordDental</span></div>
<div class="abs social"><span>Friends</span><span>Updates</span><span>Network</span><span>Circles</span></div>
<div class="abs chat">
  <div class="abs chat-person" role="img" aria-label="Receptionist with headset"></div>
  <div class="abs chat-q">Have Questions?</div>
  <div class="abs chat-btn"><small>Click Here to</small><b>Chat Online</b></div>
</div>
<div class="abs enq">
  <div class="t">
    <svg width="7" height="7" viewBox="0 0 10 10"><path d="M2 0l2 2-1 2c1 1.5 2 2.5 3 3l2-1 2 2-2 2C4 10 0 6 0 2z" fill="#3f75c4"/></svg>
    ENQUIRIES</div>
  <div class="n">Call: 555 010 22</div>
  <div class="n">Intl: +12 3 555 0147</div>
</div>

<nav class="abs nav">
  <a class="on" href="#">HOME</a><a href="#">ABOUT US</a><a href="#">THE PRACTICE</a><a href="#">ARE OF EXPERTIESE</a><a href="#">APPOINTMENT</a><a href="#">CONTACT</a>
</nav>

<!-- hero -->
<div class="abs hero"></div>
<div class="abs hero-photo" role="img" aria-label="Smiling family of three in a bright room"></div>
<div class="abs hero-copy">
  <div class="a">We Care About</div>
  <div class="b">PROIN GRAVIDA NIBH</div>
  <div class="c">lorem quis bibendum auctor, nisi elit</div>
</div>

<!-- appointment panel -->
<section class="abs panel">
  <div class="abs tab-a">Make an Appointment</div>
  <div class="abs tab-b">
    <svg width="11" height="10" viewBox="0 0 12 10"><rect x="0" y="2" width="12" height="8" rx="1" fill="#3f75c4"/><rect x="3.5" y="0" width="5" height="3" fill="#3f75c4"/><circle cx="6" cy="6" r="2.3" fill="#f2f2f2"/></svg>
    For Emergency Cases</div>

  <div class="abs col-h" style="left:13px;top:43px">
    <svg width="9" height="9" viewBox="0 0 10 10"><circle cx="5" cy="5" r="4.2" fill="none" stroke="#fff" stroke-width="1.3"/><path d="M5 2.5V5h2" stroke="#fff" fill="none"/></svg>Working Time</div>
  <div class="abs hours">
    <div><span>Monday - Friday</span><span>8.00 – 17.00</span></div>
    <div><span>Saturday</span><span>9.30 – 17.30</span></div>
    <div><span>Sunday</span><span>9.30 – 15.00</span></div>
  </div>

  <div class="abs col-h" style="left:154px;top:43px">
    <svg width="9" height="9" viewBox="0 0 10 10"><rect x="0.5" y="1.5" width="9" height="8" fill="none" stroke="#fff"/><rect x="0.5" y="1.5" width="9" height="2.5" fill="#fff"/></svg>Doctors Timetable</div>
  <div class="abs doc-text">Lorem ipsum dolor sit amet, consectetur adipiscing elit, sed do eiusmod tempor incididunt ut labore et dolore.</div>
  <div class="abs btn-w" style="left:189px;top:117px;width:63px;height:13px">View Timetable</div>

  <div class="abs col-h" style="left:273px;top:43px">
    <svg width="9" height="9" viewBox="0 0 10 10"><rect x="0.5" y="1.5" width="9" height="8" fill="none" stroke="#fff"/><rect x="0.5" y="1.5" width="9" height="2.5" fill="#fff"/></svg>Booking a Visit</div>
  <div class="abs field" style="left:273px;top:67px">Select Department</div>
  <div class="abs field" style="left:371px;top:67px">Your Phone</div>
  <div class="abs field" style="left:273px;top:92px">Full Name</div>
  <div class="abs field" style="left:371px;top:92px">mm/dd/yyyy</div>
  <div class="abs btn-w" style="left:394px;top:117px;width:63px;height:13px">Send</div>
</section>

<!-- services -->
<div class="abs sec-h" style="top:433px"><h2>Proin Gravida Nibh Auctor</h2><p>Aenean sollicitudin, lorem quis bibendum auctor, nisi elit consequat</p></div>

<article class="abs card" style="left:153px">
  <svg class="abs card-img" viewBox="0 0 117 81" role="img" aria-label="Child brushing teeth"><polygon points="0,0 117,0 117,5 36,81 0,81" fill="#e4d6c6"/><rect x="102" y="0" width="15" height="2" fill="#3f75c4"/></svg>
  <div class="abs card-title">Lorem<br>quis bibendum</div>
  <div class="abs card-body">Proin gravida nibh vel velit auctor aliquet. Aenean sollicitudin, lorem quis bibendum auctor, nisi elit consequat ipsum, nec sagittis sem nibh id elit.<br><br>Duis sed odio sit amet nibh vulputate cursus a sit amet mauris. Morbi</div>
  <div class="abs card-foot"></div><div class="abs card-more">Read more <i></i></div>
</article>
<article class="abs card" style="left:275px">
  <svg class="abs card-img" viewBox="0 0 117 81" role="img" aria-label="Dentist treating a patient"><polygon points="0,0 117,0 117,5 36,81 0,81" fill="#c9d9dc"/><rect x="102" y="0" width="15" height="2" fill="#3f75c4"/></svg>
  <div class="abs card-title">Lorem<br>quis bibendum</div>
  <div class="abs card-body">Proin gravida nibh vel velit auctor aliquet. Aenean sollicitudin, lorem quis bibendum auctor, nisi elit consequat ipsum, nec sagittis sem nibh id elit.<br><br>Duis sed odio sit amet nibh vulputate cursus a sit amet mauris. Morbi</div>
  <div class="abs card-foot"></div><div class="abs card-more">Read more <i></i></div>
</article>
<article class="abs card" style="left:397px">
  <svg class="abs card-img" viewBox="0 0 117 81" role="img" aria-label="Dental examination in progress"><polygon points="0,0 117,0 117,5 36,81 0,81" fill="#d8cfc6"/><rect x="102" y="0" width="15" height="2" fill="#3f75c4"/></svg>
  <div class="abs card-title">Lorem<br>quis bibendum</div>
  <div class="abs card-body">Proin gravida nibh vel velit auctor aliquet. Aenean sollicitudin, lorem quis bibendum auctor, nisi elit consequat ipsum, nec sagittis sem nibh id elit.<br><br>Duis sed odio sit amet nibh vulputate cursus a sit amet mauris. Morbi</div>
  <div class="abs card-foot"></div><div class="abs card-more">Read more <i></i></div>
</article>
<article class="abs card" style="left:519px">
  <svg class="abs card-img" viewBox="0 0 117 81" role="img" aria-label="Dentist in the practice"><polygon points="0,0 117,0 117,5 36,81 0,81" fill="#dccbbd"/><rect x="102" y="0" width="15" height="2" fill="#3f75c4"/></svg>
  <div class="abs card-title">Lorem<br>quis bibendum</div>
  <div class="abs card-body">Proin gravida nibh vel velit auctor aliquet. Aenean sollicitudin, lorem quis bibendum auctor, nisi elit consequat ipsum, nec sagittis sem nibh id elit.<br><br>Duis sed odio sit amet nibh vulputate cursus a sit amet mauris. Morbi</div>
  <div class="abs card-foot"></div><div class="abs card-more">Read more <i></i></div>
</article>

<!-- doctor -->
<div class="abs sec-h" style="top:694px"><h2>Proin Gravida Nibh Auctor</h2><p>Aenean sollicitudin, lorem quis bibendum auctor, nisi elit consequat</p></div>

<section class="abs box" style="left:153px;top:733px;width:304px;height:216px">
  <div class="abs doc-photo" role="img" aria-label="Patient and child at the practice"></div>
  <div class="abs doc-name"><b>Dr. Colin Ashford</b><br><span class="l1">nibh vel velit auctor aliquet.</span><br><span class="l2">Aenean sollicitudin</span></div>
  <div class="abs" style="left:12px;top:107px;width:282px;height:1px;background:#e3e3e3"></div>
  <div class="abs doc-text2">Lorem ipsum dolor sit amet, consectetur adipiscing elit. Nam risus nisl, porttitor et fermentum sem, sit amet suscipit odio suscipit id. Maecenas viverra elementum varius. Donec feugiat consequat nisi, non fringilla metus iaculis et.<br><br>Curabitur in sem vitae libero malesuada ullamcorper. Proin sit amet nibh felis. Vestibulum tortor sem, bibendum vitae pharetra non, hendrerit id magna. Morbi accumsan nisl a metus luctus ac iaculis nisi</div>
  <div class="abs gold-link" style="left:11px;top:190px">Read more »</div>
</section>

<section class="abs box appt" style="left:463px;top:733px;width:172px;height:216px">
  <h3 class="abs" style="left:16px;top:30px">Make an Appointment</h3>
  <p class="abs" style="left:17px;top:54px;width:142px;font-size:5.8px;line-height:7.4px">Lorem ipsum dolor sit amet, consectetur adipisicing elit, sed do eiusmod tempor incididunt ut labore et dolore magna aliqua. Ut enim ad minim veniam, quis nostrud exercitation ullamco laboris nisi ut aliquip ex ea commodo consequat.</p>
  <div class="abs pill" style="top:98px;background:var(--gold-light)">
    <svg width="8" height="8" viewBox="0 0 10 10"><path d="M2 0l2 2-1 2c1 1.5 2 2.5 3 3l2-1 2 2-2 2C4 10 0 6 0 2z" fill="#fff"/></svg>By Phone: +123 555 019</div>
  <div class="abs pill" style="top:120px;background:var(--gold-dark)">
    <svg width="9" height="7" viewBox="0 0 10 8"><rect width="10" height="8" rx="1" fill="#fff"/><path d="M0 0l5 4 5-4" stroke="#c98f0c" fill="none"/></svg>By email: hello@ashford.example</div>
  <p class="abs" style="left:17px;top:153px;font-size:5.8px">or fill in the form on our Appointments page:</p>
  <div class="abs btn-gold" style="left:65px;top:176px;width:85px;height:18px">Fill in the Form</div>
</section>

<!-- bottom columns -->
<div class="abs col-title" style="left:153px;top:975px">Featured article</div>
<div class="abs" style="left:153px;top:993px;width:138px;height:72px;background:linear-gradient(90deg,#d8b79c,#f0e3d8 60%,#e5e5e5)" role="img" aria-label="Smiling woman at a dental check-up"></div>
<div class="abs os" style="left:153px;top:1074px;font-size:9.5px;color:var(--gold)">Lorem quis aliquet</div>
<p class="abs" style="left:153px;top:1091px;width:140px;font-size:6.3px;line-height:8.5px">Proin gravida nibh vel velit auctor aliquet. lorem quis bibendum auctor, nisi consequat.</p>
<div class="abs" style="left:153px;top:1122px;width:138px;height:1px;background:#ddd"></div>
<svg class="abs" style="left:152px;top:1129px" width="140" height="8" viewBox="0 0 140 8">
  <path d="M1 4l4-3v6z" fill="#d9a21a"/><circle cx="63" cy="4" r="1.6" fill="#d9a21a"/><circle cx="68" cy="4" r="1.6" fill="#999"/><circle cx="73" cy="4" r="1.6" fill="#999"/><path d="M139 4l-4-3v6z" fill="#999"/>
</svg>

<div class="abs col-title" style="left:326px;top:975px">Updates</div>
<div class="abs tweet" style="top:1001px">600 sales on Nimbo SitePress! Wanna try it too? http://lnk.ex/Qa7kWp<small>14 hours ago</small></div>
<div class="abs tweet" style="top:1047px">We are so glad you like our Marlow template! Thanks, guys!!! http://lnk.ex/Rb2mTx<small>19 hours ago</small></div>
<div class="abs tweet" style="top:1093px">We are so glad you like our Marlow template! Thanks, guys!!! http://lnk.ex/Rb2mTx<small>25 hours ago</small></div>

<div class="abs col-title" style="left:499px;top:975px">Quick contacts</div>
<div class="abs label" style="left:499px;top:1001px">Your email <em>*</em></div>
<div class="abs input" style="left:499px;top:1014px;width:137px;height:17px">enter your email</div>
<div class="abs label" style="left:499px;top:1045px">Message <em>*</em></div>
<div class="abs input" style="left:499px;top:1059px;width:137px;height:63px">type your message here</div>
<div class="abs gold-link" style="left:499px;top:1127px;color:var(--blue-text);border-color:var(--blue-text)">Send Message »</div>

<!-- footer -->
<div class="abs footer-line"></div>
<div class="abs footer-copy">Copy © all right reserved AshfordDental</div>
<svg class="abs to-top" viewBox="0 0 18 18"><path d="M5.5 10.5L9 7l3.5 3.5" stroke="#fff" stroke-width="1.5" fill="none"/></svg>
<div class="abs footer-bar"></div>

</body>
</html>
```